Website Re-design for Kids Playhouse Business

Need current website which looks very outdated to be re-designed to look modern and contemporary, reduce clutter significantly and make it look elegant and simple.
Current website: http://www.tumblenest.com.au/
A website which the business owner likes, use as reference/inspiration: http://vexa.com.au/
Looking for light green palette, natural colours. "WHAT'S ON" page/link no longer required.
Industry/Entity Type
Business
Number of Pages Required
5+ page
Look and feel
Each slider illustrates characteristics of the customer's brand and the style your logo design should communicate.

```html
<!DOCTYPE html>
<html lang="en">
<head>
<meta charset="utf-8">
<title>Tumble Nest Playhouse &amp; Cafe</title>
<link rel="stylesheet" href="https://fonts.googleapis.com/css2?family=Quicksand:wght@500;600;700&family=Roboto:wght@400;500&family=Montserrat:wght@500;600;700&display=swap">
<style>
:root{
  --green:#7ab548;
  --green-dark:#69a43a;
  --green-soft:#a9d57a;
  --green-tint:#c9e6a5;
  --cream:#f8fcef;
  --white:#ffffff;
  --ink:#555a50;
  --field-border:#d9dcd2;
  --logo-red:#d9252a;
}
*{box-sizing:border-box;margin:0;padding:0}
html,body{width:1200px;height:2236px;overflow:hidden}
body{position:relative;background:var(--cream);font-family:'Roboto',Arial,sans-serif;color:var(--ink)}

/* header */
.site-header{position:absolute;left:0;top:0;width:1200px;height:150px;background:var(--cream);border-top:3px solid var(--green)}
.utility-bar{position:absolute;top:0;left:655px;width:545px;height:47px;background:var(--green);clip-path:polygon(0 0,100% 0,100% 100%,28px 100%);display:flex;align-items:center;justify-content:flex-end;gap:32px;padding-right:70px}
.utility-bar a{color:var(--white);font-size:11.5px;font-weight:500;text-decoration:none;text-transform:uppercase;letter-spacing:.2px}
.brand{position:absolute;left:86px;top:22px;display:flex;align-items:center;gap:12px}
.brand-mark{width:26px;height:26px;background:var(--green)}
.brand-name{font-family:'Quicksand',sans-serif;font-weight:700;font-size:30px;color:var(--logo-red)}
.main-nav{position:absolute;top:85px;left:360px;height:42px;display:flex;align-items:center}
.main-nav a{font-size:11.5px;font-weight:500;color:var(--ink);text-decoration:none;text-transform:uppercase;margin-right:48px;white-space:nowrap}
.eclub-button{position:absolute;left:979px;top:85px;width:134px;height:42px;background:var(--green);color:var(--white);font-size:11.5px;font-weight:500;display:flex;align-items:center;justify-content:center;text-transform:uppercase}

/* hero */
.hero{position:absolute;left:0;top:149px;width:1200px;height:517px;overflow:hidden}
.hero-photo{position:absolute;inset:0;background:
  radial-gradient(circle at 15% 30%,#e8a93b 0,transparent 22%),
  radial-gradient(circle at 85% 25%,#f2c84b 0,transparent 25%),
  radial-gradient(circle at 35% 60%,#d9c06a 0,transparent 30%),
  radial-gradient(circle at 68% 62%,#d8643f 0,transparent 30%),
  radial-gradient(circle at 90% 80%,#7fc1a8 0,transparent 22%),
  linear-gradient(120deg,#c9b65e,#e0bf6e 50%,#d49d5a)}
.hero-wave{position:absolute;left:0;top:0;width:1200px;height:14px}
.hero-text{position:absolute;left:0;right:0;top:300px;text-align:center;color:var(--white)}
.hero-title{font-family:'Quicksand',sans-serif;font-weight:700;font-size:56px;line-height:1;text-shadow:0 2px 4px rgba(0,0,0,.25)}
.hero-tagline{margin-top:22px;font-family:'Montserrat',sans-serif;font-weight:600;font-size:23px;text-transform:uppercase;text-shadow:0 1px 3px rgba(0,0,0,.3)}
.slider-dots{position:absolute;top:486px;left:0;right:0;display:flex;justify-content:center;gap:4px}
.slider-dots span{width:15px;height:15px;border:2px solid var(--white);border-radius:50%}
.slider-dots span.active{background:rgba(255,255,255,.4)}

/* about */
.about{position:absolute;left:0;top:666px;width:1200px;height:618px;background:var(--green);text-align:center;color:var(--white)}
.section-title{font-family:'Quicksand',sans-serif;font-weight:700;font-size:28px}
.about .section-title{margin-top:46px}
.about-text{width:760px;margin:26px auto 0;font-size:11.5px;line-height:25px}
.feature-list{position:absolute;left:0;top:244px;width:1200px;list-style:none}
.feature{position:absolute;width:300px;text-align:center}
.feature-photo{width:250px;height:250px;margin:0 auto;border-radius:50%;border:3px solid var(--white)}
.feature-caption{margin-top:20px;font-family:'Quicksand',sans-serif;font-weight:600;font-size:20px;line-height:29px}

/* testimonials */
.testimonials{position:absolute;left:0;top:1284px;width:1200px;height:339px;overflow:hidden;text-align:center;color:var(--white)}
.testimonials-bg{position:absolute;inset:0;background:linear-gradient(180deg,#b6dc8a 0%,#a6d373 55%,#98ca62 100%)}
.testimonials .section-title{position:relative;margin-top:55px}
.quote{position:relative;width:760px;margin:42px auto 0;font-size:11.5px;line-height:25px}
.quote-mark{position:absolute;font-family:Georgia,serif;font-size:34px;font-weight:700;line-height:1}
.quote-mark.open{left:-24px;top:-6px}
.quote-mark.close{right:0;bottom:-22px}
.quote-author{position:relative;margin-top:24px;font-family:'Quicksand',sans-serif;font-weight:600;font-size:17px}
.arrow{position:absolute;top:125px;width:24px;height:96px}
.arrow.prev{left:133px}.arrow.next{left:1050px}

/* contact */
.contact{position:absolute;left:0;top:1623px;width:1200px;height:423px;background:var(--cream);text-align:center}
.contact .section-title{margin-top:28px;color:var(--green)}
.title-rule{width:97px;height:3px;background:var(--green);margin:12px auto 0}
.contact-lead{margin-top:16px;font-size:14.5px;color:var(--ink)}
.contact-form{position:absolute;left:247px;top:153px;width:705px}
.field{position:absolute;height:45px;background:var(--white);border:1px solid var(--field-border);border-radius:2px;font-size:11.5px;color:var(--ink);display:flex;align-items:center;padding-left:17px;text-align:left}
.submit{position:absolute;left:275px;top:183px;width:156px;height:44px;background:var(--green);color:var(--white);font-size:13px;font-weight:500;display:flex;align-items:center;justify-content:center;letter-spacing:.5px}

/* footer */
.site-footer{position:absolute;left:0;top:2046px;width:1200px;height:190px;background:var(--green);color:var(--white);font-family:'Montserrat',sans-serif}
.contact-item{position:absolute;top:22px;display:flex;gap:16px}
.icon-circle{width:53px;height:53px;border:1.5px solid var(--white);border-radius:50%;display:flex;align-items:center;justify-content:center;flex:none}
.contact-label{font-size:17px;font-weight:600;margin-top:-3px}
.contact-detail{font-size:11.5px;font-weight:600;line-height:22px}
.footer-rule{position:absolute;left:88px;top:126px;width:1024px;height:1px;background:rgba(255,255,255,.25)}
.copyright{position:absolute;top:150px;left:0;right:0;text-align:center;font-family:'Roboto',sans-serif;font-size:11.5px}
</style>
</head>
<body>

<header class="site-header">
  <nav class="utility-bar">
    <a>School&nbsp; Holiday Program</a>
    <a>Specials &amp; Promotions</a>
    <a>Gallery</a>
  </nav>
  <div class="brand">
    <span class="brand-mark"></span>
    <span class="brand-name">Tumble Nest</span>
  </div>
  <nav class="main-nav">
    <a>Home</a><a>Hours&nbsp; &amp; Prices</a><a>Party Packages</a><a>Party&nbsp; Rooms</a><a>Vacation&nbsp; Care</a>
  </nav>
  <a class="eclub-button">Join our e-club</a>
</header>

<section class="hero">
  <div class="hero-photo" role="img" aria-label="Photo of two children playing with colourful foam building blocks"></div>
  <svg class="hero-wave" viewBox="0 0 1200 14" preserveAspectRatio="none" aria-hidden="true">
    <path fill="#f8fcef" d="M0 0H1200V6 Q1190 14 1180 6 T1160 6 T1140 6 T1120 6 T1100 6 T1080 6 T1060 6 T1040 6 T1020 6 T1000 6 T980 6 T960 6 T940 6 T920 6 T900 6 T880 6 T860 6 T840 6 T820 6 T800 6 T780 6 T760 6 T740 6 T720 6 T700 6 T680 6 T660 6 T640 6 T620 6 T600 6 T580 6 T560 6 T540 6 T520 6 T500 6 T480 6 T460 6 T440 6 T420 6 T400 6 T380 6 T360 6 T340 6 T320 6 T300 6 T280 6 T260 6 T240 6 T220 6 T200 6 T180 6 T160 6 T140 6 T120 6 T100 6 T80 6 T60 6 T40 6 T20 6 T0 6Z"/>
  </svg>
  <div class="hero-text">
    <h1 class="hero-title">Tumble Nest</h1>
    <p class="hero-tagline">Sydney's newest and best party &amp; play centre!</p>
  </div>
  <div class="slider-dots"><span></span><span class="active"></span><span></span></div>
</section>

<section class="about">
  <h2 class="section-title">About Tumble Nest Playhouse &amp; Cafe</h2>
  <p class="about-text">Tumble Nest is an indoor Kids Play Centre and Cafe that offers both kids and adults a chance to enjoy their time, together! We pride ourselves in offering the best indoor play centre for your kids to engage in fun and learning activities in a specially created environment that is not only warm and safe but also enhances and stimulates creativity and curiosity in a child.</p>
  <ul class="feature-list">
    <li class="feature" style="left:108px">
      <div class="feature-photo" role="img" aria-label="Photo of a family birthday party with a cake" style="background:radial-gradient(circle at 50% 60%,#c89a5a,#4a3a30 75%)"></div>
      <p class="feature-caption">Birthdays &amp;<br>Private Parties</p>
    </li>
    <li class="feature" style="left:452px">
      <div class="feature-photo" role="img" aria-label="Photo of a decorated party room with balloons" style="background:radial-gradient(circle at 50% 45%,#d45a8a,#6a3a6a 75%)"></div>
      <p class="feature-caption">4 kids loving<br>party rooms themes</p>
    </li>
    <li class="feature" style="left:796px">
      <div class="feature-photo" role="img" aria-label="Photo of costumed characters at a holiday program" style="background:radial-gradient(circle at 50% 50%,#c9b9a0,#b2302a 70%)"></div>
      <p class="feature-caption">We host school<br>holiday programs</p>
    </li>
  </ul>
</section>

<section class="testimonials">
  <div class="testimonials-bg" role="img" aria-label="Photo of a child kicking a football on grass, tinted green"></div>
  <h2 class="section-title">Our Testimonials</h2>
  <svg class="arrow prev" viewBox="0 0 24 96" aria-hidden="true"><path d="M22 2 L2 48 L22 94" fill="none" stroke="#fff" stroke-width="1.5"/></svg>
  <svg class="arrow next" viewBox="0 0 24 96" aria-hidden="true"><path d="M2 2 L22 48 L2 94" fill="none" stroke="#fff" stroke-width="1.5"/></svg>
  <blockquote class="quote">
    <span class="quote-mark open">&ldquo;</span>
    Love this place, lots of variety for the kids especially in school holidays !! They'll be entertained for hours whilst you enjoy delicious food or a great coffee !! Highly recommend it !!Love this place, lots of variety for the kids especially in school holidays !! They'll be entertained for hours whilst you enjoy delicious food or a great coffee !! Highly recommend it !!
    <span class="quote-mark close">&rdquo;</span>
  </blockquote>
  <p class="quote-author">Maria Delancey</p>
</section>

<section class="contact">
  <h2 class="section-title">Contact Us</h2>
  <div class="title-rule"></div>
  <p class="contact-lead">Our postal address and contact details</p>
  <form class="contact-form">
    <div class="field" style="left:0;top:0;width:348px">First Name:</div>
    <div class="field" style="left:358px;top:0;width:347px">Last Name :</div>
    <div class="field" style="left:0;top:60px;width:348px">Phone :</div>
    <div class="field" style="left:358px;top:60px;width:347px">Email :</div>
    <div class="field" style="left:0;top:116px;width:705px">Message :</div>
    <div class="submit" style="top:183px">SUBMIT</div>
  </form>
</section>

<footer class="site-footer">
  <div class="contact-item" style="left:87px">
    <span class="icon-circle"><svg width="16" height="20" viewBox="0 0 16 20" aria-hidden="true"><path d="M8 1a6 6 0 0 0-6 6c0 4.5 6 12 6 12s6-7.5 6-12a6 6 0 0 0-6-6z" fill="none" stroke="#fff" stroke-width="1.6"/><circle cx="8" cy="7" r="2" fill="#fff"/></svg></span>
    <div><p class="contact-label">Address :</p><p class="contact-detail">14 Fernleaf Road Lakemba 2195 NSW Australia.</p></div>
  </div>
  <div class="contact-item" style="left:481px">
    <span class="icon-circle"><svg width="18" height="14" viewBox="0 0 18 14" aria-hidden="true"><rect x="1" y="1" width="16" height="12" rx="1.5" fill="none" stroke="#fff" stroke-width="1.6"/><path d="M1.5 2 L9 8 L16.5 2" fill="none" stroke="#fff" stroke-width="1.6"/></svg></span>
    <div><p class="contact-label">Email</p><p class="contact-detail">General : hello@tumblenestplay.com</p></div>
  </div>
  <div class="contact-item" style="left:832px">
    <span class="icon-circle"><svg width="18" height="18" viewBox="0 0 18 18" aria-hidden="true"><path d="M4 1.5l3 3.5-1.8 2a10 10 0 0 0 5.8 5.8l2-1.8 3.5 3-1.8 2.5C8 16 2 10 1.5 3.3z" fill="#fff"/></svg></span>
    <div><p class="contact-label">Phone</p><p class="contact-detail">Mobile : 02 5550 0148<br>Fax: 02 5550 0149</p></div>
  </div>
  <div class="footer-rule"></div>
  <p class="copyright">© Copyright 2018 Tumble Nest All Rights Reserved</p>
</footer>

</body>
</html>
```